Moldran Foods needs a new label for canned pineapple

We want a very tasty (in terms of making your mouth water) and clean design (less is more) for our canned pineapple under the new logo of Moldran Leafline division

Target Market(s)

The company’s mission is to bring quality food to target audiences of any social status (you receive a bit more than what you spend). Our core values are: reliability, loyalty and commitment to development.
The product is sold to mainstream and lower Mainstream customers.

Requirements
Must have
• The design should take into consideration the visibility on the shelf among competitor products (brief file) and that the product is a MAINSTREAM product.
We want a very tasty (in terms of making your mouth water) and clean design (less is more). The design should be easily modifiable for other canned fruits or vegetables.
The package must display on the front the following elements listed in the order of their should have noticeability:
• Moldran Leaf logo
• Pineapple picture
• Product name
Designers should take into account that the shelfs for displaying the products in the shops may have an elevation of up to 3 cm that can overlap the product label.

Guidelines
• We would like the packaging to be as simple as possible (or at least not to sabotage the Moldran name ), as our strategy depends on the agressive communication of the Moldran logo.
• We would also like to communicate through suggestive and optimal colours as to be easily spotted on the shelf.
• As we have quite a minimal communication budget we need basically for the packaging to do a lot of the communication job itself
• FMCG is a highly visual industry so we have to include pictures of the products on the packages (even more than others do, as we are focused on health and quality - we want people to have that feeling of fresh products even though we are selling canned ones)
Should not have
• but the minimum amount of text on the front.

```html
<!DOCTYPE html>
<html lang="en">
<head>
<meta charset="utf-8">
<title>Moldran Leafline Pineapple Slices Label</title>
<link rel="stylesheet" href="https://fonts.googleapis.com/css2?family=Oswald:wght@500;600;700&family=Cinzel:wght@600;700&display=swap">
<style>
  :root {
    --label-yellow: #f2c21a;
    --label-yellow-light: #ffd83a;
    --label-yellow-deep: #e0a80c;
    --shield-green: #0f5a1f;
    --shield-green-dark: #0a4316;
    --shield-rim: #3f9a2a;
    --shield-rim-light: #7cc23a;
    --title-yellow: #f4ef2a;
    --logo-white: #ffffff;
    --leaf-green: #3f8a2c;
    --leaf-green-dark: #1f5a1a;
    --fruit-gold: #f3d35a;
    --fruit-pale: #fbeaa2;
    --weight-ink: #1c2a0c;
  }
  * { margin: 0; padding: 0; box-sizing: border-box; }
  html, body {
    width: 1200px;
    height: 1200px;
    overflow: hidden;
  }
  body {
    position: relative;
    background: radial-gradient(ellipse at 50% 40%, var(--label-yellow-light) 0%, var(--label-yellow) 55%, var(--label-yellow-deep) 100%);
    font-family: "Oswald", sans-serif;
  }
  .leaf-crown {
    position: absolute;
    top: 40px;
    width: 320px;
    height: 340px;
    background: radial-gradient(ellipse at 50% 30%, var(--leaf-green) 0%, var(--leaf-green-dark) 70%, transparent 72%);
  }
  .leaf-crown--left { left: 20px; }
  .leaf-crown--right { right: 20px; }
  .shield {
    position: absolute;
    left: 120px;
    top: 150px;
    width: 960px;
    height: 800px;
  }
  .brand {
    position: absolute;
    left: 0;
    width: 1200px;
    top: 250px;
    display: flex;
    justify-content: center;
    align-items: center;
    gap: 18px;
  }
  .brand-dot {
    width: 46px;
    height: 46px;
    border-radius: 50%;
    background: var(--shield-rim-light);
  }
  .brand-name {
    font-family: "Oswald", sans-serif;
    font-weight: 600;
    font-size: 78px;
    color: var(--logo-white);
    line-height: 1;
  }
  .product-name {
    position: absolute;
    left: 0;
    width: 1200px;
    top: 430px;
    text-align: center;
    font-family: "Oswald", sans-serif;
    font-weight: 700;
    font-size: 108px;
    line-height: 1;
    color: var(--title-yellow);
    letter-spacing: -1px;
  }
  .product-style {
    position: absolute;
    left: 0;
    width: 1200px;
    top: 590px;
    text-align: center;
    font-family: "Cinzel", serif;
    font-weight: 600;
    font-size: 44px;
    letter-spacing: 6px;
    color: var(--title-yellow);
  }
  .divider {
    position: absolute;
    left: 400px;
    width: 400px;
    top: 660px;
    height: 3px;
    background: var(--title-yellow);
  }
  .quality {
    position: absolute;
    left: 0;
    width: 1200px;
    top: 680px;
    text-align: center;
    font-family: "Cinzel", serif;
    font-weight: 700;
    font-size: 32px;
    letter-spacing: 5px;
    color: var(--title-yellow);
  }
  .fruit-photo {
    position: absolute;
    left: 80px;
    top: 760px;
    width: 1040px;
    height: 330px;
    border-radius: 40px 40px 0 0;
    background: radial-gradient(ellipse at 50% 60%, var(--fruit-pale) 0%, var(--fruit-gold) 55%, var(--label-yellow-deep) 100%);
  }
  .net-weight {
    position: absolute;
    left: 0;
    width: 1200px;
    top: 1112px;
    text-align: center;
    font-family: "Oswald", sans-serif;
    font-weight: 600;
    font-size: 40px;
    color: var(--weight-ink);
  }
</style>
</head>
<body>
  <div class="leaf-crown leaf-crown--left" role="img" aria-label="Pineapple crown leaves"></div>
  <div class="leaf-crown leaf-crown--right" role="img" aria-label="Pineapple crown leaves"></div>

  <svg class="shield" viewBox="0 0 960 800" aria-hidden="true">
    <defs>
      <linearGradient id="shieldFill" x1="0" y1="0" x2="0" y2="1">
        <stop offset="0" stop-color="#137026"/>
        <stop offset="1" stop-color="#0a4316"/>
      </linearGradient>
    </defs>
    <path d="M40 80 Q480 -20 920 80 L920 640 Q480 700 40 640 Z" fill="#3f9a2a"/>
    <path d="M62 100 Q480 10 898 100 L898 622 Q480 678 62 622 Z" fill="url(#shieldFill)"/>
    <path d="M160 70 Q480 20 800 70 L770 230 Q480 270 190 230 Z" fill="#0a4316" stroke="#7cc23a" stroke-width="6"/>
  </svg>

  <div class="brand">
    <span class="brand-dot"></span>
    <span class="brand-name">Moldran Leafline</span>
  </div>

  <h1 class="product-name">PINEAPPLE SLICES</h1>
  <p class="product-style">IN LIGHT SYRUP</p>
  <div class="divider"></div>
  <p class="quality">PREMIUM QUALITY</p>

  <div class="fruit-photo" role="img" aria-label="Halved pineapples and pineapple chunks"></div>

  <p class="net-weight">NET WT. 20 OZ (1 LB. 4 OZ.) 567G</p>
</body>
</html>
```